wealth management firm, professional group, new model

we have a logo that works but we need a card, white background using our colors...clean look

our tag line if can be used in

Steady Guidance for Every Stage

```html
<!DOCTYPE html>
<html lang="en">
<head>
<meta charset="utf-8">
<title>Halvern Capital Group – Business Card</title>
<link href="https://fonts.googleapis.com/css2?family=Montserrat:wght@400;500;700&display=swap" rel="stylesheet">
<style>
  :root {
    --navy: #0f1f4d;
    --paper: #f4f5f7;
    --white: #ffffff;
    --backdrop: #7d7d7d;
  }
  * { margin: 0; padding: 0; box-sizing: border-box; }
  html, body {
    width: 1200px; height: 1050px; overflow: hidden;
    background: var(--backdrop);
    font-family: "Montserrat", sans-serif;
  }
  .canvas { position: relative; width: 1200px; height: 1050px; }
  .card {
    position: absolute; left: 250px; width: 700px; height: 400px;
    box-shadow: 0 14px 30px rgba(0,0,0,0.28);
  }
  /* Front */
  .card-front { top: 70px; background: var(--navy); color: var(--white); }
  .front-brand {
    position: absolute; top: 130px; left: 0; width: 100%; text-align: center;
    font-weight: 500; font-size: 44px; letter-spacing: 1px; line-height: 1.1;
  }
  .tagline-rule {
    position: absolute; left: 0; right: 0; top: 282px;
    display: flex; align-items: center; gap: 14px;
  }
  .tagline-rule .rule { flex: 1; height: 1.5px; background: var(--white); }
  .tagline-rule .tagline {
    font-weight: 400; font-size: 17px; letter-spacing: 1px; white-space: nowrap;
  }
  /* Back */
  .card-back { top: 570px; background: var(--paper); color: var(--navy); }
  .back-brand {
    position: absolute; top: 52px; left: 48px;
    font-weight: 500; font-size: 28px; letter-spacing: 0.5px; line-height: 1.1;
  }
  .address {
    position: absolute; left: 48px; top: 250px; font-style: normal;
    font-weight: 500; font-size: 16px; line-height: 1.6;
  }
  .person { position: absolute; left: 400px; top: 150px; }
  .person-name { font-weight: 700; font-size: 26px; letter-spacing: 0.5px; }
  .person-role { font-weight: 500; font-size: 16px; margin-top: 2px; }
  .contacts {
    position: absolute; left: 400px; top: 270px; list-style: none;
    font-weight: 500; font-size: 17px; line-height: 1.65;
  }
  .contacts li { display: flex; align-items: center; gap: 8px; }
  .contacts .phone { letter-spacing: 3px; }
  .contacts svg { width: 14px; height: 14px; fill: var(--navy); flex: none; }
</style>
</head>
<body>
<main class="canvas">
  <section class="card card-front">
    <div class="front-brand">Halvern Capital Group</div>
    <div class="tagline-rule">
      <span class="rule"></span>
      <span class="tagline">Steady Guidance for Every Stage</span>
      <span class="rule"></span>
    </div>
  </section>

  <section class="card card-back">
    <div class="back-brand">Halvern Capital Group</div>
    <address class="address">
      480 N Lakeview Rd<br>Maple Grove, FL 32014
    </address>
    <div class="person">
      <div class="person-name">DANIEL HOLLIS</div>
      <div class="person-role">Advisor</div>
    </div>
    <ul class="contacts">
      <li class="phone">
        <svg viewBox="0 0 16 16" aria-hidden="true"><path d="M3.6 1.2l2.2 2.6-1.3 1.6c.9 2 2.3 3.4 4.2 4.3l1.5-1.3 2.6 2.2-1.3 2.6C6.6 13 3 9.4 2.2 2.5z"/></svg>
        555-014-2287
      </li>
      <li>
        <svg viewBox="0 0 16 16" aria-hidden="true"><path d="M1 3h14v10H1z M2.5 4.5v.4L8 9l5.5-4.1v-.4z" fill-rule="evenodd"/></svg>
        info@halverncapital.com
      </li>
      <li>
        <svg viewBox="0 0 16 16" aria-hidden="true"><circle cx="8" cy="8" r="7"/><path d="M1 8h14M8 1v14M8 1c-3 3.5-3 10.5 0 14M8 1c3 3.5 3 10.5 0 14" stroke="#f4f5f7" stroke-width="1" fill="none"/></svg>
        halverncapital.com
      </li>
    </ul>
  </section>
</main>
</body>
</html>
```